Rollers & Glides.com

Vertical Business Card with focus on branding with our icon. Information on card will be logo, persons name, position, phone number, email address and website. Use the the name Marcus Pellow, position President, phone number 480.915.2267, email Marcus@rollersandglides-demo.com, website www.rollersandglides-demo.com.

```html
<!DOCTYPE html>
<html lang="en">
<head>
<meta charset="utf-8">
<title>Rollers &amp; Glides.com — Business Card</title>
<link rel="stylesheet" href="https://fonts.googleapis.com/css2?family=Roboto:wght@400;500;700&display=swap">
<style>
  :root {
    --bg: #cdd1d2;
    --paper: #f1f1ef;
    --brand-blue: #1f4a9e;
    --ink-blue: #1b3a8c;
    --ink: #2a2a2a;
    --white: #ffffff;
  }
  html, body {
    margin: 0;
    padding: 0;
    width: 1200px;
    height: 1051px;
    overflow: hidden;
    background: var(--bg);
    font-family: "Roboto", sans-serif;
  }
  .canvas {
    position: relative;
    width: 1200px;
    height: 1051px;
  }
  .card {
    position: absolute;
    left: 250px;
    width: 700px;
    height: 400px;
    box-sizing: border-box;
    box-shadow: 0 10px 30px rgba(0,0,0,0.18);
  }
  .card--front {
    top: 95px;
    background: var(--paper);
  }
  .card--back {
    top: 556px;
    background: var(--brand-blue);
    display: flex;
    align-items: center;
    justify-content: center;
  }
  .contact {
    position: absolute;
    left: 52px;
    top: 150px;
    color: var(--ink);
  }
  .contact__name {
    margin: 0;
    font-size: 30px;
    font-weight: 700;
    color: var(--ink-blue);
    line-height: 1.1;
  }
  .contact__title {
    margin: 2px 0 0;
    font-size: 22px;
    font-weight: 500;
    color: var(--ink);
  }
  .contact__rule {
    width: 24px;
    height: 3px;
    background: var(--ink-blue);
    margin: 12px 0 14px;
  }
  .contact__line {
    margin: 0 0 6px;
    font-size: 18px;
    display: flex;
    align-items: center;
    gap: 8px;
  }
  .contact__line svg { flex: none; }
  .contact__sep { margin-left: 6px; }
  .brand {
    display: flex;
    align-items: center;
    gap: 14px;
    font-weight: 500;
  }
  .brand__dot {
    border-radius: 50%;
    flex: none;
  }
  .brand--front {
    position: absolute;
    right: 48px;
    top: 178px;
    color: var(--ink-blue);
    font-size: 22px;
  }
  .brand--front .brand__dot {
    width: 34px;
    height: 34px;
    border: 0;
    background: var(--ink-blue);
  }
  .brand--back {
    color: var(--white);
    font-size: 40px;
    letter-spacing: 1px;
  }
  .brand--back .brand__dot {
    width: 56px;
    height: 56px;
    background: var(--white);
  }
</style>
</head>
<body>
<main class="canvas">
  <section class="card card--front" aria-label="Business card front">
    <div class="contact">
      <h1 class="contact__name">Marcus Pellow</h1>
      <p class="contact__title">President</p>
      <div class="contact__rule"></div>
      <p class="contact__line">www.rollersandglides-demo.com</p>
      <p class="contact__line">
        <svg width="16" height="14" viewBox="0 0 16 14" aria-hidden="true"><path d="M1 5c0-3 14-3 14 0v1h-4V4H5v2H1z M3 7h10l1 6H2z" fill="var(--ink-blue)"/></svg>
        480.915.2267
        <svg class="contact__sep" width="18" height="14" viewBox="0 0 18 14" aria-hidden="true"><rect x="1" y="2" width="16" height="11" fill="var(--ink-blue)"/><path d="M1 2l8 6 8-6" stroke="var(--paper)" stroke-width="1.5" fill="none"/></svg>
        Marcus@rollersandglides-demo.com
      </p>
    </div>
    <div class="brand brand--front">
      <span class="brand__dot"></span>
      <span class="brand__name">Rollers &amp; Glides.com</span>
    </div>
  </section>

  <section class="card card--back" aria-label="Business card back">
    <div class="brand brand--back">
      <span class="brand__dot"></span>
      <span class="brand__name">Rollers &amp; Glides.com</span>
    </div>
  </section>
</main>
</body>
</html>
```